Varnik Holdings — Business Card Design Brief
Overview
Design a double-sided business card for Varnik Holdings that highlights our two service arms: Varnik Communications (telecommunications) and Varnik Energy (business energy solutions). The card should feel smart and stand out when handed to clients.

Objectives
Showcase our areas of specialty clearly.
Reflect the overall Varnik / Varnik Holdings brand while acknowledging both arms.
Explore using both logos (Communications + Energy) or one unified logo, depending on the design.

Deliverables
One double-sided business card design (front + back).

Content & Copy
Front (preferred): Logo: Varnik / Varnik Holdings
Descriptor: Business Communications | Business Energy
Back:My contact details and company details
Core products: Business Mobile • Telephony • Internet • Business Energy Solutions

Brand & Visual Direction
We have a group logo currently tailored more toward telecoms, plus a separate Varnik Energy logo.
Please explore layouts that use both logos or just one, whichever works best.
Color: I wouldn't mind seeing an option using our the Blue/Purple gradient from our website (varnik-example.co.uk), but also open to non-gradient approaches and other colours..

Overall look: Smart, modern, and distinctive.
Format & Print Specs
Double-sided business card format. (Use a standard size

Must-Haves
Front: Varnik wording or Varnik Holdings wording with atleast 1 logo also on front “Business Communications | Business Energy.”

Back: Contact + company details and core products.
A design that stands out while remaining professional.

Nice-to-Have Options
A gradient version using our site’s Blue/Purple gradient.
A non-gradient version.
A dual-logo treatment versus a single-logo treatment.

Thanks
Owen

```html
<!DOCTYPE html>
<html lang="en">
<head>
<meta charset="utf-8">
<title>Varnik Holdings — Business Card</title>
<link rel="stylesheet" href="https://fonts.googleapis.com/css2?family=Montserrat:wght@400;500;700;800&display=swap">
<style>
  :root{
    --bg:#3a3a3c;
    --purple:#8b3fa3;
    --blue:#1a6aa8;
    --navy:#26246b;
    --cyan:#21a7e0;
    --sky:#2c8fd8;
    --green:#5cb543;
    --lime:#c8d42a;
    --white:#ffffff;
    --ink:#26246b;
  }
  *{margin:0;padding:0;box-sizing:border-box}
  html,body{width:1200px;height:875px;overflow:hidden;background:var(--bg);font-family:"Montserrat",sans-serif}
  .canvas{position:relative;width:1200px;height:875px;display:flex;flex-direction:column;align-items:center;justify-content:center;gap:36px}
  .card{position:relative;width:680px;height:388px;overflow:hidden;box-shadow:0 10px 30px rgba(0,0,0,.45)}

  /* front */
  .card-front{background:linear-gradient(120deg,var(--purple) 0%,#6a58a8 45%,var(--blue) 100%)}
  .brand-row{position:absolute;top:120px;left:0;right:0;display:flex;justify-content:center;align-items:center;gap:44px}
  .brand{display:flex;align-items:center;gap:14px;font-weight:700;font-size:44px;letter-spacing:1px}
  .brand-dot{width:34px;height:34px;border-radius:50%;border:6px solid currentColor}
  .brand-comms{color:var(--sky)}
  .brand-energy{color:var(--green)}
  .divider{width:1.5px;height:86px;background:var(--lime)}
  .descriptor{position:absolute;top:262px;left:0;right:0;text-align:center;font-size:19px;font-weight:500;letter-spacing:.5px}
  .descriptor .comms{color:var(--cyan)}
  .descriptor .energy{color:var(--lime)}

  /* back */
  .card-back{background:var(--white)}
  .wave{position:absolute;inset:0}
  .back-brands{position:absolute;left:40px;top:120px;display:flex;gap:34px;align-items:center}
  .back-brand{display:flex;align-items:center;gap:8px;font-weight:800;font-size:28px;color:var(--ink)}
  .back-brand .dot{width:22px;height:22px;border-radius:50%;border:4px solid var(--sky)}
  .back-brand.energy .dot{border-color:var(--green)}
  .products{position:absolute;left:46px;top:178px;list-style:none;color:var(--ink);font-size:15px;line-height:22px;font-weight:500}
  .products li::before{content:"";display:inline-block;width:5px;height:5px;border-radius:50%;background:var(--cyan);margin-right:8px;vertical-align:middle}
  .person{position:absolute;right:34px;top:24px;text-align:right;color:var(--ink)}
  .person-name{font-weight:800;font-size:28px;letter-spacing:.5px}
  .person-role{font-size:15px;font-weight:500;margin-top:2px}
  .contact{position:absolute;right:30px;top:176px;text-align:right;color:var(--white);font-size:14.5px;line-height:24px;font-weight:500}
  .contact .line{display:flex;justify-content:flex-end;align-items:center;gap:8px}
  .contact svg{width:12px;height:12px;fill:var(--cyan)}
  .contact .spacer{display:inline-block;width:12px}
</style>
</head>
<body>
<main class="canvas">

  <section class="card card-front" aria-label="Card front">
    <div class="brand-row">
      <div class="brand brand-comms"><span class="brand-dot"></span>Varnik</div>
      <span class="divider"></span>
      <div class="brand brand-energy"><span class="brand-dot"></span>Varnik</div>
    </div>
    <p class="descriptor"><span class="comms">Business Communications</span> <span class="energy">| Business Energy</span></p>
  </section>

  <section class="card card-back" aria-label="Card back">
    <svg class="wave" viewBox="0 0 680 388" preserveAspectRatio="none" aria-hidden="true">
      <defs>
        <linearGradient id="stripe-fade" gradientUnits="userSpaceOnUse" x1="300" y1="0" x2="430" y2="0">
          <stop offset="0" stop-color="#5cb543"/>
          <stop offset="1" stop-color="#21a7e0"/>
        </linearGradient>
      </defs>
      <path class="wave-stripe" d="M0,336 C160,358 270,316 360,196 C430,104 500,100 680,104" fill="none" stroke="url(#stripe-fade)" stroke-width="9"/>
      <path class="wave-band" d="M0,352 C160,374 278,332 368,212 C438,120 508,116 680,120 L680,388 L0,388 Z" fill="var(--navy)"/>
    </svg>

    <div class="person">
      <div class="person-name">DORIAN VALE</div>
      <div class="person-role">Founder/CEO</div>
    </div>

    <div class="back-brands">
      <div class="back-brand comms"><span class="dot"></span>Varnik</div>
      <div class="back-brand energy"><span class="dot"></span>Varnik</div>
    </div>

    <ul class="products">
      <li>Business Mobile</li>
      <li>Telephony</li>
      <li>Internet</li>
      <li>Business Energy Solutions</li>
    </ul>

    <div class="contact">
      <div class="line">24 Larkfield Road<span class="spacer"></span></div>
      <div class="line">Leeds England, LS2 7QB<span class="spacer"></span></div>
      <div class="line">+44 0113 555 0142
        <svg viewBox="0 0 24 24"><path d="M6.6 10.8a15.1 15.1 0 0 0 6.6 6.6l2.2-2.2a1 1 0 0 1 1-.25 11.4 11.4 0 0 0 3.6.57 1 1 0 0 1 1 1V20a1 1 0 0 1-1 1A17 17 0 0 1 3 4a1 1 0 0 1 1-1h3.5a1 1 0 0 1 1 1c0 1.25.2 2.45.57 3.57a1 1 0 0 1-.25 1z"/></svg></div>
      <div class="line">info@varnik-example.co.uk
        <svg viewBox="0 0 24 24"><path d="M2 5h20v14H2z M2 5l10 8 10-8" stroke="var(--navy)" stroke-width="1.5"/></svg></div>
      <div class="line">www.varnik-example.co.uk
        <svg viewBox="0 0 24 24"><circle cx="12" cy="12" r="10"/><path d="M2 12h20M12 2c3 3 3 17 0 20M12 2c-3 3-3 17 0 20" stroke="var(--navy)" stroke-width="1.3" fill="none"/></svg></div>
    </div>
  </section>

</main>
</body>
</html>
```